"Harbor Builders" is a residential building company and needs a new business card design and may re

We would like a redesign based on the existing logo, and would like to see a new font as well. We are bespoke home builders who build sustainable energy efficient homes.

Industry/Entity Type

Construction

Contact Information for Business Card

Business card size 40mm x 90mm

Colors

Designer to choose colors to be used in the design.

```html
<!DOCTYPE html>
<html lang="en">
<head>
<meta charset="utf-8">
<title>Harbor Builders — Business Card</title>
<link rel="stylesheet" href="https://fonts.googleapis.com/css2?family=Roboto:wght@400;500&family=Roboto+Condensed:wght@700&display=swap">
<style>
  :root {
    --backdrop: #b9a58e;
    --card-dark: #1c1c1c;
    --card-light: #f1f1f1;
    --lime: #b7d433;
    --white: #ffffff;
    --ink: #111111;
    --grey: #555555;
  }
  html, body {
    margin: 0;
    padding: 0;
    width: 1200px;
    height: 960px;
    overflow: hidden;
    background: var(--backdrop);
    font-family: "Roboto", Arial, sans-serif;
  }
  .canvas {
    position: relative;
    width: 1200px;
    height: 960px;
  }
  .card {
    position: absolute;
    width: 602px;
    height: 341px;
    box-shadow: 0 4px 10px rgba(0,0,0,0.35);
  }
  .card-front {
    left: 302px;
    top: 130px;
    background: var(--card-dark);
    color: var(--white);
  }
  .card-back {
    left: 299px;
    top: 489px;
    width: 600px;
    background: var(--card-light);
  }
  .brand {
    position: absolute;
    display: flex;
    align-items: center;
  }
  .brand-square {
    background: var(--lime);
    flex: none;
  }
  .brand-name {
    font-weight: 500;
    line-height: 1;
    white-space: nowrap;
  }
  .card-front .brand { left: 32px; top: 42px; gap: 14px; }
  .card-front .brand-square { width: 34px; height: 34px; }
  .card-front .brand-name { font-size: 28px; color: var(--white); }
  .card-back .brand { left: 112px; top: 130px; gap: 22px; }
  .card-back .brand-square { width: 62px; height: 62px; }
  .card-back .brand-name { font-size: 44px; color: var(--ink); }

  .holder-name {
    position: absolute;
    left: 31px;
    top: 122px;
    margin: 0;
    font-family: "Roboto Condensed", "Arial Narrow", sans-serif;
    font-weight: 700;
    font-size: 21px;
    color: var(--lime);
    text-transform: uppercase;
  }
  .details {
    position: absolute;
    left: 32px;
    top: 158px;
    font-size: 14px;
    line-height: 18px;
  }
  .details p { margin: 0; }
  .details .company { font-weight: 500; }
  .details .registry { margin-top: 4px; }
  .contact-list {
    list-style: none;
    margin: 6px 0 0;
    padding: 0;
  }
  .contact-list li {
    display: flex;
    align-items: center;
    gap: 8px;
    height: 19px;
  }
  .contact-list svg { width: 12px; height: 12px; flex: none; }
  .web-address {
    position: absolute;
    left: 0;
    right: 0;
    top: 297px;
    margin: 0;
    text-align: center;
    font-size: 15px;
    letter-spacing: 3px;
    color: var(--grey);
  }
</style>
</head>
<body>
<main class="canvas">
  <section class="card card-front" aria-label="Business card front">
    <div class="brand">
      <span class="brand-square"></span>
      <span class="brand-name">harbor builders</span>
    </div>
    <h1 class="holder-name">Daniel Moretti</h1>
    <div class="details">
      <p class="company">Harbor Builders Pty Ltd</p>
      <p>PO Box 4120 Eastgate</p>
      <p>LPO Bayview WA 6071</p>
      <p class="registry">Registration 40318</p>
      <p>ABN: 52 309 614 778</p>
      <ul class="contact-list">
        <li>
          <svg viewBox="0 0 12 12" aria-hidden="true"><rect x="3" y="0.5" width="6" height="11" rx="1" fill="none" stroke="var(--lime)" stroke-width="1.4"/><rect x="5" y="9" width="2" height="1" fill="var(--lime)"/></svg>
          <span>0412 555 019</span>
        </li>
        <li>
          <svg viewBox="0 0 12 12" aria-hidden="true"><rect x="0.5" y="2.5" width="11" height="7.5" fill="var(--lime)"/><path d="M0.5 2.8 L6 7 L11.5 2.8" fill="none" stroke="var(--card-dark)" stroke-width="1"/></svg>
          <span>daniel@harborbuilders.com.au</span>
        </li>
        <li>
          <svg viewBox="0 0 12 12" aria-hidden="true"><circle cx="6" cy="6" r="5.5" fill="var(--lime)"/><path d="M3 3.5 Q5 4 4.5 6 Q6 7 5 9 M7.5 2 Q8 4 9.5 5" fill="none" stroke="var(--card-dark)" stroke-width="1"/></svg>
          <span>www.harborbuilders.com.au</span>
        </li>
      </ul>
    </div>
  </section>

  <section class="card card-back" aria-label="Business card back">
    <div class="brand">
      <span class="brand-square"></span>
      <span class="brand-name">harbor builders</span>
    </div>
    <p class="web-address">www.harborbuilders.com.au</p>
  </section>
</main>
</body>
</html>
```